2 x Digitize Logo | 2 x Business Cards | 2 x Fridge Magnets

We require 6 deliverables:
1. Residential logo redrawn (same just high quality for large print format).
2. Corporate logo redrawn (minor changes to wording and high quality for large print format).
3. New business card design for Furniture Removals (residential)
4. New business card design for Corporate Relocations (business)
5. New Fridge magnet for Furniture removals (residential)
6. New fridge magnet for Corporate Relocations (business)
1. Residential Logo
a. We require the logo to be translated into a high quality digital image with no modifications.
(see attached resilogo.jpg)
2. Residential Logo
a. We require the logo to be edited (add the word corporate relocations) be translated into a high quality digital image.
(see attached corplogo.jpg)
3. Using the resilogo please make a new business card for our business.
a. Please see the web site https://www.larkbendcarters.com.au for colours and inspiration.
b. The residential business card needs the following information:
i. Business Name (using the residential logo).
ii. Free Call: 1800 LB Cart (the L, B and Cart much be the same colour as the logo).
iii. Website: www.LarkbendCarters.com.au
iv. Address: 4/17 Ormsdale Court, VIC 3264
v. Email: cart@LarkbendCarters.com.au
vi. backof Card:
Review our service
www.PennantOrbit.com.au
Services: Local, Country, Interstate | Furniture Removals | Piano, Billiard Tables & Antiques
4. Using the corplogo please make a new business card for our business.
b. The corporate business card needs the following information:
i. Business Name (using the corporate logo).
v. Email: corporate@LarkbendCarters.com.au
vi. Back of Card:
Review our service
www.PennantOrbit.com.au
Services: Corporate relocations | Office equipment moves | Packing Service | Packing Materials
5. Using the resilogo please make a new fridge magent for our business.
b. The residential fidge magnet needs the following information:
iv. Services: Local, Country, Interstate | Furniture Removals | Piano, Billiard Tables & Antiques
6. Using the corplogo please make a new fridge magent for our business.
b. The corporate fidge magnet needs the following information:
iv. Services: Local, Country, Interstate | Corporate relocations
Target Market(s)
Residential Furniture Removals and Corporate Office relocations
Industry/Entity Type
Business
Contact Information for Business Card
Please see full brief for six items required
Requirements
Must have
- Clean simple, easy to read
Nice to have
- fresh, stand out, eye catching
Should not have
- plain, standard, boring, general

```html
<!DOCTYPE html>
<html lang="en">
<head>
<meta charset="utf-8">
<title>Larkbend Carters – Corporate Relocations Business Card</title>
<link rel="stylesheet" href="https://fonts.googleapis.com/css2?family=Open+Sans:wght@400;600&display=swap">
<style>
  :root {
    --brand-green: #04773f;
    --brand-red: #c4151c;
    --card-white: #ffffff;
    --ink: #1f1f1f;
    --backdrop: #ece7df;
  }
  * { box-sizing: border-box; margin: 0; padding: 0; }
  html, body {
    width: 1200px; height: 900px; overflow: hidden;
    background: var(--backdrop);
    font-family: "Open Sans", Arial, sans-serif;
  }
  .stage {
    position: relative; width: 1200px; height: 900px;
  }
  .card {
    position: absolute; top: 285px;
    width: 540px; height: 330px;
    overflow: hidden;
    box-shadow: 0 6px 18px rgba(0,0,0,.18);
  }
  /* Back of card */
  .card-back {
    left: 45px;
    background: var(--brand-green);
    color: var(--card-white);
    text-align: center;
    padding-top: 78px;
  }
  .review-label {
    color: var(--brand-red); font-size: 13px; letter-spacing: .3px;
  }
  .review-url { font-size: 19px; margin-top: 2px; }
  .services-heading {
    display: flex; align-items: center; justify-content: center;
    gap: 8px; margin-top: 30px;
    color: var(--brand-red); font-size: 12px; letter-spacing: .5px;
  }
  .services-heading::before, .services-heading::after {
    content: ""; width: 52px; height: 1px; background: var(--brand-red);
  }
  .services-list {
    list-style: none; margin-top: 8px;
    font-size: 15px; line-height: 18px; text-transform: uppercase;
  }
  /* Front of card */
  .card-front { left: 615px; background: var(--card-white); }
  .card-front .wave { position: absolute; inset: 0; }
  .brand {
    position: absolute; top: 46px; right: 34px;
    display: flex; align-items: center; gap: 10px;
  }
  .brand-mark { width: 14px; height: 14px; background: var(--brand-red); }
  .brand-name {
    color: var(--brand-green); font-weight: 600; font-size: 19px;
    letter-spacing: .6px; text-transform: uppercase;
  }
  .contact {
    position: absolute; left: 34px; top: 128px;
    list-style: none; color: var(--ink); font-size: 18px;
  }
  .contact li {
    display: flex; align-items: center; gap: 10px; height: 31px;
  }
  .contact svg { width: 14px; height: 14px; fill: var(--brand-red); flex: none; }
  .hl-green { color: var(--brand-green); }
  .hl-red { color: var(--brand-red); }
</style>
</head>
<body>
<main class="stage">

  <section class="card card-back" aria-label="Back of business card">
    <p class="review-label">Review Our Service</p>
    <p class="review-url">www.PennantOrbit.com.au</p>
    <p class="services-heading">SERVICES</p>
    <ul class="services-list">
      <li>Corporate Relocations</li>
      <li>Office Equipment Moves</li>
      <li>Packing Service</li>
      <li>Packing Materials</li>
    </ul>
  </section>

  <section class="card card-front" aria-label="Front of business card">
    <svg class="wave" viewBox="0 0 540 330" preserveAspectRatio="none" aria-hidden="true">
      <path fill="var(--brand-green)" d="M0 330 V322 C190 318 360 250 540 150 V330 Z"/>
      <path fill="var(--brand-red)" d="M0 262 C110 296 250 290 420 215 C290 282 150 300 0 300 Z"/>
    </svg>

    <div class="brand">
      <span class="brand-mark"></span>
      <span class="brand-name">Larkbend Carters</span>
    </div>

    <ul class="contact">
      <li>
        <svg viewBox="0 0 24 24"><path d="M6.6 10.8a15.1 15.1 0 0 0 6.6 6.6l2.2-2.2c.3-.3.7-.4 1-.2 1.1.4 2.3.6 3.6.6.6 0 1 .4 1 1V20c0 .6-.4 1-1 1A17 17 0 0 1 3 4c0-.6.4-1 1-1h3.5c.6 0 1 .4 1 1 0 1.3.2 2.5.6 3.6.1.3 0 .7-.2 1z"/></svg>
        <span>1800 <span class="hl-red">L</span><span class="hl-green">B</span> <span class="hl-red">Cart</span> / 1800 52 40 19</span>
      </li>
      <li>
        <svg viewBox="0 0 24 24"><path d="M2 5h20v14H2z M2 5l10 8 10-8" fill="var(--brand-red)"/><path d="M3 6l9 7 9-7" fill="none" stroke="#fff" stroke-width="1.6"/></svg>
        <span>corporate@LarkbendCarters.com.au</span>
      </li>
      <li>
        <svg viewBox="0 0 24 24"><circle cx="12" cy="12" r="10"/><path d="M2 12h20M12 2c3 3 3 17 0 20M12 2c-3 3-3 17 0 20" fill="none" stroke="#fff" stroke-width="1.4"/></svg>
        <span>www.LarkbendCarters.com.au</span>
      </li>
      <li>
        <svg viewBox="0 0 24 24"><path d="M12 2a7 7 0 0 0-7 7c0 5 7 13 7 13s7-8 7-13a7 7 0 0 0-7-7zm0 9.5A2.5 2.5 0 1 1 12 6.5a2.5 2.5 0 0 1 0 5z"/></svg>
        <span>4/17 Ormsdale Court, VIC 3264</span>
      </li>
    </ul>
  </section>

</main>
</body>
</html>
```